Business Card for Professional Domainer

Require a business card design for an Individual Person who is a Professional Domainer.

Who is a Professional Domainer?
A domainer is someone who earns a profit buying and selling domain names.
Professional Domainer are the ones who do this on a full time basis.

So we require the business card design to be related to the above work.

There is no company or any logo currently, as the card is required for an Individual Person.

Business Card required to mention following details:

1. Full Name of the Person (Ex: Marisol Pike)
2. Education Qualification (Ex: B.Tech Computer Science)
3. Mobile Number (Ex: +71 4837062915)
4. Website (Ex: www.brivolta.example)
5. Email (Ex: contact@brivolta.example)

Positioning of the details:

1. Mobile Number should be placed to Right Top Corner
2. Education Qualification should be just below Full Name
3. Website and Email should be on Bottom Part, on a bar at the bottom

It's important to include images related to the nature of work (Domaining) in the card design.
A good related image would be great. Image should be either in background or as a logo.
The image should be focus of the business card, and shoudl speak out on itself.
Anyone looking at the card should understand at one look what work is being done.
So kindly use images in the design which are highly relevant to domaining and domain names.

Along with the image, it's also good if you use the word "Professional Domainer" anywhere in the design.
Maybe along with the image or somewhere it would fit. These words would be like company name.
So please try to use these words "Professional Domainer" in the design, as it will help a lot.

Colors: Blue, Red, Green

We like these colors, but you are free to use any color which would be good for the design.

Card design should be according to PressaLine specs:

Document Trim Size = 91 x 55 mm | 1075 x 650 pixels
Full Bleed Size = 94 x 58 mm | 1110 x 685 pixels

Last thing, the business card should look professional and clean.
People should know that the person is a Professional Domainer at one look of the card.

Thank You and All the Best :)

Message to the the designers working on this project:

We have now guaranteed this project. This means, we will 100% choose a design and award the project to the one we like the best. So kindly submit your best designs before Wednesday, 3 July 2013. After that we are going to finalize the project and award to the best one. So please hurry up so that you are not too late. Thank You and All the Best!

```html
<!DOCTYPE html>
<html lang="en">
<head>
<meta charset="utf-8">
<title>Marisol Pike – Professional Domainer Business Card</title>
<link rel="stylesheet" href="https://fonts.googleapis.com/css2?family=Montserrat:wght@600;700&family=Questrial&display=swap">
<style>
  :root {
    --page-bg: #e9ecee;
    --card-dark: #1e3b46;
    --card-mid: #2c5563;
    --card-glow: #3b6a78;
    --band-light: #4f94a6;
    --frame-line: #5a9db0;
    --ink-white: #f4f8f9;
    --ink-navy: #163440;
    --photo-deep: #17323c;
    --photo-mid: #3a6f7d;
    --photo-light: #6aa3b1;
  }
  * { margin: 0; padding: 0; box-sizing: border-box; }
  html, body {
    width: 1200px; height: 900px; overflow: hidden;
    background: var(--page-bg);
  }
  .canvas {
    position: relative; width: 1200px; height: 900px;
    display: flex; flex-direction: column; align-items: center; justify-content: center; gap: 40px;
  }
  .card {
    position: relative; width: 640px; height: 387px; overflow: hidden;
    box-shadow: 0 6px 18px rgba(0,0,0,0.18);
  }

  /* Back side */
  .card-back__photo {
    position: absolute; inset: 0;
    background:
      radial-gradient(circle at 40% 38%, rgba(255,230,200,0.55) 0, rgba(255,230,200,0) 18%),
      radial-gradient(ellipse at 45% 45%, var(--photo-light) 0, var(--photo-mid) 35%, var(--photo-deep) 85%);
  }

  /* Front side */
  .card-front {
    background: radial-gradient(ellipse at 65% 40%, var(--card-glow) 0, var(--card-mid) 40%, var(--card-dark) 100%);
    font-family: "Montserrat", sans-serif;
    color: var(--ink-white);
  }
  .contact-strip {
    position: absolute; top: 0; bottom: 0; left: 0; width: 42px;
    background: var(--card-dark);
  }
  .contact-band {
    position: absolute; top: 0; bottom: 0; left: 42px; width: 78px;
    background: var(--band-light);
  }
  .contact-line {
    position: absolute; bottom: 22px;
    writing-mode: vertical-rl; transform: rotate(180deg);
    white-space: nowrap; font-weight: 700;
  }
  .contact-line--web { left: 11px; font-size: 17px; color: var(--ink-white); }
  .contact-line--mail { left: 48px; font-size: 16px; color: var(--ink-white); }
  .contact-line--phone { left: 76px; font-size: 27px; color: var(--ink-navy); letter-spacing: 0.5px; }

  .title-frame {
    position: absolute; left: 292px; top: 12px; width: 330px; height: 318px;
    border: 5px solid var(--frame-line);
  }
  .tagline {
    position: absolute; left: 318px; top: 34px;
    font-size: 40px; line-height: 1.08; font-weight: 700;
  }
  .holder {
    position: absolute; left: 228px; top: 262px;
  }
  .holder__name {
    font-size: 53px; font-weight: 700; line-height: 1; white-space: nowrap;
  }
  .holder__degree {
    font-family: "Questrial", sans-serif;
    font-size: 24px; margin-top: 4px; letter-spacing: 0.3px;
  }
</style>
</head>
<body>
  <main class="canvas">
    <section class="card card-back">
      <div class="card-back__photo" role="img" aria-label="Photograph of a hand in a dark suit touching glowing device and domain icons on a teal screen"></div>
    </section>

    <section class="card card-front">
      <div class="contact-strip"></div>
      <div class="contact-band"></div>
      <p class="contact-line contact-line--web">www.brivolta.example</p>
      <p class="contact-line contact-line--mail">contact@brivolta.example</p>
      <p class="contact-line contact-line--phone">+71 4837062915</p>

      <div class="title-frame"></div>
      <h1 class="tagline">Professional<br>Domainer</h1>

      <div class="holder">
        <h2 class="holder__name">Marisol Pike</h2>
        <p class="holder__degree">B.Tech Computer Science</p>
      </div>
    </section>
  </main>
</body>
</html>
```